KDWB Business Card

Looking for a business card design to incorporate our branding. We want to only use the colors listing in the Branding Package (attached).
Updates

Target Market(s)

People who need their phone or device fixed.

Industry/Entity Type

Electronics

Contact Information for Business Card

Please use:

Brightwick Gadget Clinic LLC
4810 E Harlow Ridge Rd
Suite 417
San Antonio, TX 78163

Marcus Delgrove, Store Manager

(210) 555-0147

Requirements
Must have
• Must include the colors that are contained within the Branding Package PDF file.

```html
<!DOCTYPE html>
<html lang="en">
<head>
<meta charset="utf-8">
<title>Brightwick Gadget Clinic – Business Card</title>
<link rel="stylesheet" href="https://fonts.googleapis.com/css2?family=Varela+Round&display=swap">
<style>
  :root {
    --page-bg: #e9e6e1;
    --card-bg: #f3f1ee;
    --brand-red: #d3301f;
    --brand-red-deep: #b8200f;
    --band-dark: #2f3133;
    --ink: #1f1f1f;
    --light-text: #f6efe9;
    --soft-text: #f1d2c8;
    --outline: #e8c7b8;
  }
  * { box-sizing: border-box; margin: 0; padding: 0; }
  html, body {
    width: 1200px; height: 970px; overflow: hidden;
    background: var(--page-bg);
    font-family: "Varela Round", sans-serif;
  }
  .card {
    position: absolute; left: 80px; top: 188px;
    width: 1040px; height: 594px;
    background: var(--card-bg);
    overflow: hidden;
    box-shadow: 0 10px 30px rgba(0,0,0,.18);
  }
  .brand {
    position: absolute; left: 55px; top: 92px;
    display: flex; align-items: center; gap: 28px;
  }
  .brand-square {
    width: 124px; height: 124px; border-radius: 22px;
    background: var(--brand-red);
  }
  .brand-name {
    font-size: 50px; color: var(--brand-red); letter-spacing: -0.5px;
    line-height: 1.1;
  }
  .name-band {
    position: absolute; left: 0; top: 311px;
    width: 748px; height: 61px;
    background: var(--band-dark);
    clip-path: polygon(0 0, 100% 0, 96% 100%, 0 100%);
    display: flex; align-items: center; padding-left: 55px;
    color: var(--light-text);
  }
  .person-name { font-size: 32px; }
  .divider { width: 2px; height: 36px; background: var(--light-text); margin: 0 16px 0 20px; }
  .person-role { font-size: 26px; }
  .info-panel {
    position: absolute; left: 0; top: 376px;
    width: 722px; height: 218px;
    background: linear-gradient(180deg, var(--brand-red) 0%, var(--brand-red-deep) 100%);
    padding: 12px 0 0 54px;
    color: var(--light-text);
  }
  .company { font-size: 30px; margin-bottom: 20px; }
  .address { font-size: 26px; line-height: 35px; color: var(--soft-text); }
  .phone {
    display: flex; align-items: center; gap: 12px;
    margin-top: 12px; font-size: 26px; color: var(--soft-text);
  }
  .phone svg { width: 32px; height: 30px; }
  .accent-tile {
    position: absolute; left: 742px; top: 302px;
    width: 320px; height: 320px; border-radius: 46px;
    background: linear-gradient(160deg, var(--brand-red) 0%, var(--brand-red-deep) 100%);
  }
  .accent-tile::after {
    content: ""; position: absolute; inset: 24px;
    border: 3px solid var(--outline); border-radius: 34px;
  }
</style>
</head>
<body>
  <div class="card">
    <div class="brand">
      <div class="brand-square"></div>
      <div class="brand-name">Brightwick Gadget Clinic</div>
    </div>

    <div class="name-band">
      <span class="person-name">Marcus Delgrove</span>
      <span class="divider"></span>
      <span class="person-role">Store Manager</span>
    </div>

    <div class="info-panel">
      <p class="company">Brightwick Gadget Clinic LLC</p>
      <p class="address">4810 E Harlow Ridge Rd<br>Suite 417, San Antonio, TX 78163</p>
      <p class="phone">
        <svg viewBox="0 0 32 30" aria-hidden="true">
          <rect x="1" y="1" width="30" height="28" rx="5" fill="var(--soft-text)"/>
          <path d="M7 11c0-3 4-5 9-5s9 2 9 5l-4 1-1-3h-8l-1 3z" fill="var(--brand-red)"/>
          <rect x="10" y="14" width="12" height="9" rx="2" fill="var(--brand-red)"/>
        </svg>
        (210) 555-0147
      </p>
    </div>

    <div class="accent-tile"></div>
  </div>
</body>
</html>
```